Chorefinch clone for Asia

I am developing a clone for www.chorefinchly.example. It is meant for Asia (i.e. Singapore, Australia, Indonesian, Philippines, Malaysia).

I need a webdesign that functionally look like chorefinch, but localised with pictures of Asian of multi country (rather than latin american looks).

The color, iconography, images can be different, but the functionality must be all be similar to www.chorefinchly.example

I need a mobile UI as well that is for a mobile app, again, similar to that of chorefinch mobile app.

Note that I need the design for the following pages:
1. homepage
2. login page
3. page after login in.
4. search page & results
5. post a task & confirmation page
6. Payment page
7. User Review page.
8. Sign up page.

The webpages are to be in english....

The features must have photos of friendly looking helpers.

Target Market(s)

Asian countries. To serve a mass market, for part time, one off task job.

Requirements
Must have
• Just use ChoreFinchAsia for the name of the site for Starters. I have not arrived at a name yet.

```html
<!DOCTYPE html>
<html lang="en">
<head>
<meta charset="utf-8">
<title>ChoreFinchAsia – Home</title>
<link rel="stylesheet" href="https://fonts.googleapis.com/css2?family=Arimo:wght@400;700&family=Tinos:wght@700&display=swap">
<style>
:root{
  --page:#f3f3f3;
  --band:#e6e6e6;
  --ink:#555;
  --ink-soft:#777;
  --nav:#5a86a8;
  --list:#3d6f93;
  --accent:#2aa3d3;
  --btn:#3aa6cc;
  --btn-dark:#2b8fb5;
  --panel:#e4e4e4;
  --head-dark:#22495f;
  --caption:rgba(40,40,40,.78);
  --line:#cfcfcf;
}
*{box-sizing:border-box;margin:0;padding:0}
html,body{width:949px;height:1200px;overflow:hidden}
body{position:relative;background:var(--page);font-family:"Arimo",Arial,sans-serif;color:var(--ink)}
.abs{position:absolute}

.header-bg{left:0;top:0;width:949px;height:600px;
  background:linear-gradient(180deg,#d9dcde 0,#eceeef 45%,#f3f3f3 100%)}
.header-glow{left:470px;top:0;width:479px;height:232px;
  background:radial-gradient(circle at 80% 20%,#6d93a6 0,#2d4a58 45%,#1d2f38 70%,rgba(29,47,56,0) 100%),
  linear-gradient(90deg,rgba(30,50,60,0),#26404c 35%)}
.header-glow-soft{left:230px;top:20px;width:280px;height:90px;border-radius:50%;
  background:radial-gradient(ellipse,rgba(140,185,205,.45),rgba(140,185,205,0) 70%)}

.brand{left:53px;top:62px;display:flex;align-items:center;gap:10px}
.brand-dot{width:22px;height:22px;border-radius:50%;background:#4fa3dc}
.brand-name{font-size:34px;font-weight:700;color:#111;letter-spacing:.5px}

.top-nav{left:65px;top:133px;font-size:16px;color:var(--nav)}
.top-nav span{margin:0 7px;color:#7a9cb5}

.quick-links{left:588px;top:95px;display:flex;align-items:center;font-size:14px;color:#fff}
.quick-links .icon-cart{width:44px;height:40px;border-radius:4px;background:linear-gradient(#c9a25c,#8a6a38)}
.quick-links .label{margin-left:14px}
.quick-links .divider{width:1px;height:36px;background:#b9c7cd;margin:0 18px}
.quick-links .reviews{color:#8fc24a;margin-left:12px}

.slider{left:62px;top:161px;width:540px;height:312px;background:#fff;border:1px solid #cfcfcf;box-shadow:0 4px 8px rgba(0,0,0,.15)}
.slider-photo{left:7px;top:7px;width:540px;height:304px;
  background:linear-gradient(120deg,#eef0f1 0,#dfe3e5 45%,#b9c6cf 70%,#e4e8ea 100%)}
.slider-caption{left:7px;top:243px;width:540px;height:61px;background:var(--caption);color:#fff;padding:8px 15px}
.slider-caption h2{font-family:"Tinos",Georgia,serif;font-size:17px;letter-spacing:.5px}
.slider-caption p{font-size:15px;margin-top:6px}
.slider-dots{left:410px;top:221px;display:flex;gap:8px}
.slider-dots i{width:11px;height:11px;border-radius:50%;background:#eee;border:1px solid #bbb;display:block}
.slider-dots i.on{background:#2a8fc0;border-color:#2a8fc0}

.browse{left:588px;top:151px;width:309px;height:393px;background:linear-gradient(#ececec,#dcdcdc);box-shadow:0 6px 10px rgba(0,0,0,.18)}
.browse-head{left:598px;top:171px;width:306px;height:38px;background:linear-gradient(#4d7a96,#26506a);
  color:#fff;font-weight:700;font-size:23px;text-align:center;line-height:38px;box-shadow:0 3px 4px rgba(0,0,0,.3)}
.task-list{left:609px;top:224px;width:276px;list-style:none}
.task-list li{height:30.2px;line-height:24px;padding-left:58px;font-size:15.5px;color:var(--list);border-bottom:1px dotted #9a9a9a}
.task-list li:last-child{border-bottom:none}
.btn-categories{left:783px;top:531px;width:108px;height:23px;background:var(--btn);color:#fff;font-size:12.5px;text-align:center;line-height:23px;box-shadow:2px 2px 0 #c7c7c7}

.contact{left:72px;top:503px}
.contact h3{font-size:18px;font-weight:400;color:var(--accent)}
.contact p{font-size:21px;color:#666;margin-top:12px}

.signup-icon{left:289px;top:506px}
.signup-title{left:341px;top:508px;font-size:15px;color:var(--accent)}
.signup-form{left:310px;top:531px;width:232px;height:33px;background:#fff;border:1px solid #c9c9c9;box-shadow:inset 0 1px 2px rgba(0,0,0,.08)}
.signup-form .placeholder{left:12px;top:10px;font-size:10px;color:#888}
.signup-form .submit{right:3px;top:4px;width:52px;height:24px;background:linear-gradient(#5cc4f0,#1d9ad6);color:#fff;font-size:13px;text-align:center;line-height:24px;border-radius:2px}

.features{left:0;top:600px;width:949px;height:289px;background:var(--band);border-top:1px solid #cfcfcf;border-bottom:1px solid #cfcfcf}
.feature{top:24px;width:240px}
.feature-art{margin-left:55px;width:100px;height:100px}
.feature-art.doc{background:linear-gradient(135deg,#fafafa,#cfd6dc);transform:rotate(-10deg);width:78px;height:88px;margin-top:6px}
.feature-art.folder{background:linear-gradient(135deg,#dbe9f2,#8fb3c9);transform:skewX(-12deg);width:70px;height:92px;margin-left:75px}
.feature h4{margin-top:33px;font-size:13px;color:var(--accent)}
.feature p{margin-top:20px;font-size:10px;line-height:15.5px;color:#666}
.btn{display:block;width:108px;height:24px;background:var(--btn);color:#fff;font-weight:700;font-size:13px;line-height:24px;padding-left:16px;box-shadow:3px 3px 0 #c4c4c4}
.feature .btn{margin-top:22px}

.info{top:924px;width:380px}
.info h4{font-size:13px;font-weight:400;color:#888}
.info p{margin-top:12px;font-size:11px;line-height:14.7px;color:#666;text-align:justify}
.info .btn{margin-top:29px}

.footer-rule{left:0;top:1117px;width:949px;height:12px;border-top:1px solid #ddd;border-bottom:1px solid #ddd;background:#f6f6f6}
.footer-links{left:75px;top:1152px;font-size:10px;color:#888;word-spacing:2px}
.footer-legal{right:56px;top:1152px;font-size:10px;color:#888}
</style>
</head>
<body>
<div class="abs header-bg"></div>
<div class="abs header-glow"></div>
<div class="abs header-glow-soft"></div>

<div class="abs brand"><span class="brand-dot"></span><span class="brand-name">ChoreFinchAsia</span></div>

<nav class="abs top-nav">How it works<span>|</span>Sign up<span>|</span>Log in</nav>

<div class="abs quick-links">
  <div class="icon-cart" role="img" aria-label="Shopping cart filled with groceries"></div>
  <span class="label">Household Shoping</span>
  <span class="divider"></span>
  <svg width="38" height="36" viewBox="0 0 38 36" aria-hidden="true"><polygon points="19,1 24,13 37,13 26,21 30,35 19,27 8,35 12,21 1,13 14,13" fill="#8cc63f" stroke="#5b8f1f" stroke-width="1.5"/></svg>
  <span class="reviews">Reviews</span>
</div>

<div class="abs slider">
  <div class="abs slider-photo" role="img" aria-label="Photo of two friendly helpers in blue shirts fixing up a bright room with a power drill"></div>
  <div class="abs slider-dots"><i></i><i></i><i class="on"></i><i></i><i></i><i></i></div>
  <div class="abs slider-caption">
    <h2>Some Great Title Here</h2>
    <p>Manus oput alt et quisit lorem ipsum dolorest at magnum</p>
  </div>
</div>

<div class="abs browse"></div>
<div class="abs browse-head">Browse Tasks....</div>
<ul class="abs task-list">
  <li>Delivery</li><li>House Chores</li><li>Shopping</li><li>Office Help</li><li>Handyman</li>
  <li>Moving Help</li><li>Virtual Assistance</li><li>Event Help</li><li>Skilled</li>
</ul>
<div class="abs btn-categories">View All Categories</div>

<div class="abs contact"><h3>Get in touch!</h3><p>+ 00000000</p></div>

<svg class="abs signup-icon" width="48" height="36" viewBox="0 0 48 36" aria-hidden="true">
  <path d="M2 10 L24 2 L46 10 L46 34 L2 34 Z" fill="#1f3f66"/>
  <path d="M2 10 L24 24 L46 10" fill="none" stroke="#fff" stroke-width="2"/>
</svg>
<div class="abs signup-title">Get Started</div>
<div class="abs signup-form">
  <span class="abs placeholder">enter your email adress here</span>
  <span class="abs submit">Submit</span>
</div>

<section class="abs features">
  <div class="abs feature" style="left:82px">
    <div class="feature-art doc" role="img" aria-label="Notepad with a pencil"></div>
    <h4>How ChoreFinch works</h4>
    <p>industry. Lorem Ipsum has been the industry's standard dummy text ever since the 1500s, when an unknow the industry's standard dummy text ever since the 1500s</p>
    <span class="btn">Read More</span>
  </div>
  <div class="abs feature" style="left:373px">
    <svg style="margin-left:50px" width="72" height="88" viewBox="0 0 72 88" aria-hidden="true">
      <path d="M36 3 L68 14 L68 42 C68 64 52 78 36 85 C20 78 4 64 4 42 L4 14 Z" fill="#6fb43f" stroke="#3f7a1e" stroke-width="3"/>
      <path d="M20 44 L32 56 L54 30" fill="none" stroke="#fff" stroke-width="8" stroke-linecap="round" stroke-linejoin="round"/>
    </svg>
    <h4 style="margin-top:45px">Secured</h4>
    <p>industry. Lorem Ipsum has been the industry's standard dummy text ever since the 1500s, when an unknow the industry's standard dummy text ever since the 1500s</p>
    <span class="btn">Read More</span>
  </div>
  <div class="abs feature" style="left:668px">
    <div class="feature-art folder" role="img" aria-label="Light blue document folder"></div>
    <h4 style="margin-top:37px">Busines Details</h4>
    <p>industry. Lorem Ipsum has been the industry's standard dummy text ever since the 1500s, when an unknow the industry's standard dummy text ever since the 1500s</p>
    <span class="btn">Read More</span>
  </div>
</section>

<section class="abs info" style="left:81px">
  <h4>Recent Tasks</h4>
  <p>Lorem ipsum dolor sit amet, consectetur adipisicing elit, sed do eiusmod tempor incididunt ut labore et dolore magna aliqua. Ut enim ad minim veniam, quis nostrud exercitation ullamco laboris nisi ut aliquip ex ea commodo consequat. Duis aute irure dolor in reprehenderit in voluptate velit esse cillum dolore eu fugiat nulla pariatur. Excepteur sint occaecat cupidatat non proident, sunt in culpa qui officia deserunt mollit anim id est laborum</p>
  <span class="btn">Read More</span>
</section>
<section class="abs info" style="left:521px">
  <h4>Welcome</h4>
  <p>Lorem ipsum dolor sit amet, consectetur adipisicing elit, sed do eiusmod tempor incididunt ut labore et dolore magna aliqua. Ut enim ad minim veniam, quis nostrud exercitation ullamco laboris nisi ut aliquip ex ea commodo consequat. Duis aute irure dolor in reprehenderit in voluptate velit esse cillum dolore eu fugiat nulla pariatur. Excepteur sint occaecat cupidatat non proident, sunt in culpa qui officia deserunt mollit anim id est laborum</p>
  <span class="btn">Read More</span>
</section>

<div class="abs footer-rule"></div>
<div class="abs footer-links">Option &nbsp;Option &nbsp;Option Option &nbsp;Option &nbsp;Option Option</div>
<div class="abs footer-legal">Copyright Statement | Terms &amp; Conditions</div>
</body>
</html>
```